UI/ UX Design for ERP Software

We need a new UX/UI interface for a ERP software for property managers. Our CMMS / ERP solution is made based on responsive design technologies and is coded in PHP.
The overall UX to be similar to Tev Ulna - easy navigation, intuitive menus.

Industry/Entity Type

Property Management

Number of Pages Required

5+ page

Requirements
Must have
• Round dock buttons
Consistent icons across the application
Enough Spacing between buttons/icons/ menu
Consistent Font
Nice to have
• We would like the UX to allow the users to use the application without /minimum training.
Should not have
• we don't want anything that is classic with respect to UX

```html
<!DOCTYPE html>
<html lang="en">
<head>
<meta charset="utf-8">
<title>Domora – Property ERP</title>
<link href="https://fonts.googleapis.com/css2?family=Inter:wght@400;500;600;700&display=swap" rel="stylesheet">
<style>
:root{
  --page:#1d1d25;
  --window:#26262f;
  --panel:#1f1f27;
  --card:#31323d;
  --tile:#34343e;
  --icon:#f6ecd0;
  --text:#ffffff;
  --muted:#9aa3c0;
  --accent:#1a8cff;
  --orange:#ff7a2e;
  --dock:#1c1c23;
}
*{box-sizing:border-box;margin:0;padding:0}
html,body{width:1200px;height:1200px;overflow:hidden;background:var(--page);font-family:"Inter",sans-serif;color:var(--text)}
.window{position:absolute;left:207px;width:787px;background:var(--window);border-radius:24px}
.window--nav{top:42px;height:475px}
.window--property{top:549px;height:594px}
.dots{position:absolute;left:24px;top:9px;display:flex;gap:4px}
.dots span{width:7px;height:7px;border-radius:50%}
.dots .y{background:#f7c531}.dots .r{background:#f0443c}.dots .g{background:#35c94a}
.brand{position:absolute;left:25px;top:30px;display:flex;align-items:center;gap:5px;font-size:13px;font-weight:600}
.brand i{width:10px;height:10px;border-radius:50%;background:var(--text);display:block}
.theme-toggle{position:absolute;left:565px;top:32px;width:47px;height:17px;border-radius:9px;background:#1e1e25;display:flex;align-items:center;justify-content:space-between;padding:0 7px}
.theme-toggle .off{width:11px;height:11px;border-radius:50%;border:1.5px solid #4a4a55}
.welcome{position:absolute;left:624px;top:34px;font-size:9px;font-weight:500}
.welcome b{font-weight:700}
.avatar{position:absolute;left:732px;top:26px;width:29px;height:29px;border-radius:50%;background:radial-gradient(circle at 50% 40%,#b07a58,#4a3a33 70%);box-shadow:0 2px 6px rgba(0,0,0,.5)}
.heading{position:absolute;left:0;right:0;top:69px;text-align:center;font-size:13px;font-weight:700}
.nav-panel{position:absolute;left:160px;top:91px;width:468px;height:294px;background:var(--panel);border-radius:12px;padding:18px 0 0 33px}
.tiles{display:grid;grid-template-columns:repeat(6,70.5px);grid-auto-rows:67px}
.tile{display:flex;flex-direction:column;align-items:center}
.tile .box{width:46px;height:46px;border-radius:11px;background:var(--tile);display:flex;align-items:center;justify-content:center}
.tile svg{width:20px;height:20px;fill:var(--icon)}
.tile .label{margin-top:5px;font-size:7px;font-weight:500;white-space:nowrap}
.tile.active .label{font-weight:700;color:var(--icon)}
.tile.start2{grid-column-start:2}
.dock{position:absolute;left:330px;width:125px;height:49px;border-radius:12px;background:var(--dock);display:flex;align-items:center;justify-content:center;gap:27px}
.window--nav .dock{top:408px}
.window--property .dock{top:526px}
.dock-btn{width:32px;height:32px;border-radius:9px;display:flex;align-items:center;justify-content:center}
.dock-btn svg{width:18px;height:18px;fill:#fff}
.dock-btn.home{background:linear-gradient(160deg,#22b3ff,#0f7ef0)}
.dock-btn.apps{background:linear-gradient(160deg,#ff9a3d,#f0612a)}
.page-title{position:absolute;left:28px;top:67px;display:flex;align-items:center;gap:9px;font-size:13px;font-weight:700}
.back{width:13px;height:13px;border-radius:50%;background:#fff;display:flex;align-items:center;justify-content:center}
.tabs{position:absolute;left:30px;top:101px;width:740px;display:flex;flex-wrap:wrap;gap:10px 6px}
.tab{height:24px;border-radius:5px;background:var(--panel);font-size:7px;font-weight:600;display:flex;align-items:center;justify-content:center}
.tab.current{background:var(--accent)}
.info-card{position:absolute;left:29px;top:173px;width:455px;height:338px;background:var(--card);border-radius:10px}
.info-card h2{position:absolute;left:20px;top:16px;font-size:11px;font-weight:700}
.edit-link{position:absolute;right:19px;top:16px;display:flex;align-items:center;gap:5px;font-size:7.5px;font-weight:600;text-decoration:underline}
.edit-link svg{width:13px;height:13px}
.fields{position:absolute;top:49px;left:24px;display:grid;grid-template-columns:152px 132px 140px;grid-auto-flow:column;grid-template-rows:repeat(11,25.8px)}
.field dt{font-size:7px;font-weight:700;line-height:10px}
.field dd{font-size:7px;color:var(--muted);line-height:10px;font-weight:500}
.photo{position:absolute;width:125px;height:83px;border-radius:6px}
.photo.p1{left:499px;top:175px;background:linear-gradient(180deg,#2a58a8,#1a2540 60%,#8a4a2a)}
.photo.p2{left:634px;top:175px;background:linear-gradient(180deg,#a8b4cc,#8d8d90 50%,#3aa4df)}
.photo.p3{left:499px;top:270px;background:linear-gradient(135deg,#e8e6e2,#a9a6a0 70%,#6f6c68)}
.photo.p4{left:634px;top:270px;background:linear-gradient(180deg,#4f7fbf,#a6bfd9 55%,#6e6558)}
</style>
</head>
<body>

<section class="window window--nav">
  <div class="dots"><span class="y"></span><span class="r"></span><span class="g"></span></div>
  <div class="brand"><i></i>Domora</div>
  <div class="theme-toggle"><span class="off"></span><svg width="11" height="11" viewBox="0 0 24 24"><path fill="#fff" d="M14 2a10 10 0 1 0 8 15A9 9 0 0 1 14 2z"/></svg></div>
  <div class="welcome">Welcome, <b>Rafe Dalton</b></div>
  <div class="avatar" role="img" aria-label="User profile photo"></div>
  <h1 class="heading">Start navigation</h1>

  <div class="nav-panel">
    <div class="tiles">
      <div class="tile"><div class="box"><svg viewBox="0 0 24 24"><circle cx="12" cy="8" r="3.2"/><circle cx="5" cy="9" r="2.4"/><circle cx="19" cy="9" r="2.4"/><path d="M6 19c0-4 2.7-6 6-6s6 2 6 6z"/><path d="M1 17c0-3 1.8-4.5 4-4.5 1 0 1.8.3 2.4.8C6 14.6 5.2 16 5 17z"/><path d="M23 17c0-3-1.8-4.5-4-4.5-1 0-1.8.3-2.4.8 1.4 1.3 2.2 2.7 2.4 3.7z"/></svg></div><span class="label">Customers</span></div>
      <div class="tile"><div class="box"><svg viewBox="0 0 24 24"><path d="M5 2h14v20h-5v-4h-4v4H5zm3 3v2h2V5zm6 0v2h2V5zM8 9v2h2V9zm6 0v2h2V9zM8 13v2h2v-2zm6 0v2h2v-2z" fill-rule="evenodd"/></svg></div><span class="label">Properties</span></div>
      <div class="tile active"><div class="box"><svg viewBox="0 0 24 24"><path d="M12 2a10 10 0 1 0 0 20 10 10 0 0 0 0-20zm0 4a3.5 3.5 0 1 1 0 7 3.5 3.5 0 0 1 0-7zm0 14a8 8 0 0 1-6-2.7C7 15.4 9.3 14.5 12 14.5s5 .9 6 2.8A8 8 0 0 1 12 20z"/></svg></div><span class="label">Tenants</span></div>
      <div class="tile"><div class="box"><svg viewBox="0 0 24 24"><circle cx="12" cy="7" r="4.5"/><path d="M3 22c0-5 4-8 9-8s9 3 9 8z"/></svg></div><span class="label">Contacts</span></div>
      <div class="tile"><div class="box"><svg viewBox="0 0 24 24"><circle cx="9" cy="13" r="4.5" fill="none" stroke="#f6ecd0" stroke-width="4" stroke-dasharray="2.4 1.4"/><circle cx="9" cy="13" r="4"/><circle cx="9" cy="13" r="1.8" fill="#34343e"/><circle cx="18.5" cy="6" r="2.8" fill="none" stroke="#f6ecd0" stroke-width="2.6" stroke-dasharray="1.5 1"/><circle cx="18.5" cy="17.5" r="2.8" fill="none" stroke="#f6ecd0" stroke-width="2.6" stroke-dasharray="1.5 1"/></svg></div><span class="label">Contractors</span></div>
      <div class="tile"><div class="box"><svg viewBox="0 0 24 24"><circle cx="8.5" cy="8" r="3.8"/><circle cx="17" cy="8.5" r="3"/><path d="M1 20c0-4 3.3-6.5 7.5-6.5S16 16 16 20z"/><path d="M17 13c3.5 0 6 2 6 5.5h-5.5c0-2-.7-4-2.2-5.3.5-.1 1.1-.2 1.7-.2z"/></svg></div><span class="label">Employees</span></div>

      <div class="tile"><div class="box"><svg viewBox="0 0 24 24"><path d="M21 6.5a5.5 5.5 0 0 1-7.3 5.2L5.4 20a2 2 0 0 1-2.8-2.8l8.3-8.3A5.5 5.5 0 0 1 17.5 2l-3.3 3.3.8 3 3 .8L21.3 5.8c0 .2-.3.5-.3.7z"/></svg></div><span class="label">Maintenance</span></div>
      <div class="tile"><div class="box"><svg viewBox="0 0 24 24"><path d="M9 3h6a1.5 1.5 0 0 1 1.5 1.5V6H21a1 1 0 0 1 1 1v5h-8v-1h-4v1H2V7a1 1 0 0 1 1-1h4.5V4.5A1.5 1.5 0 0 1 9 3zm0 1.8V6h6V4.8zM2 13.5h8V15h4v-1.5h8V20a1 1 0 0 1-1 1H3a1 1 0 0 1-1-1z"/></svg></div><span class="label">Works orders</span></div>
      <div class="tile"><div class="box"><svg viewBox="0 0 24 24"><text x="12" y="20" text-anchor="middle" font-size="21" font-weight="700" font-family="Inter,sans-serif" fill="#f6ecd0">$</text></svg></div><span class="label">Purcharse orders</span></div>
      <div class="tile"><div class="box"><svg viewBox="0 0 24 24"><circle cx="10" cy="10" r="6" fill="none" stroke="#f6ecd0" stroke-width="3"/><path d="M14 15.5l1.5-1.5 6 6-1.5 1.5z"/></svg></div><span class="label">Inspections</span></div>
      <div class="tile"><div class="box"><svg viewBox="0 0 24 24"><path d="M12 2l11 19H1z"/><rect x="11" y="8.5" width="2" height="7" fill="#34343e"/><rect x="11" y="17" width="2" height="2" fill="#34343e"/></svg></div><span class="label">Risk management</span></div>
      <div class="tile"><div class="box"><svg viewBox="0 0 24 24"><path d="M5 4h3.5a3.5 3.5 0 0 1 7 0H19v18H5z"/><g fill="#34343e"><rect x="8" y="9" width="2" height="2"/><rect x="11" y="9" width="5" height="2"/><rect x="8" y="13" width="2" height="2"/><rect x="11" y="13" width="5" height="2"/><rect x="8" y="17" width="2" height="2"/><rect x="11" y="17" width="5" height="2"/></g></svg></div><span class="label">Compliance</span></div>

      <div class="tile start2"><div class="box"><svg viewBox="0 0 24 24"><path d="M3 3h18v12l-6 6H3z"/><path d="M15 15h6l-6 6z" fill="#34343e"/></svg></div><span class="label">Tenant requests</span></div>
      <div class="tile"><div class="box"><svg viewBox="0 0 24 24"><path d="M5 2h9l5 5v15H5zm9 0v5h5"/><text x="12" y="19" text-anchor="middle" font-size="11" font-weight="700" font-family="Inter,sans-serif" fill="#34343e">$</text></svg></div><span class="label">Budgeting</span></div>
      <div class="tile"><div class="box"><svg viewBox="0 0 24 24"><path d="M2 5l1.3-1.3L4.5 5 7 2.5 8.3 3.8 4.5 7.6zm0 7l1.3-1.3L4.5 12 7 9.5l1.3 1.3-3.8 3.8z"/><rect x="10" y="4" width="12" height="2.4"/><rect x="10" y="11" width="12" height="2.4"/><rect x="10" y="18" width="12" height="2.4"/><circle cx="5" cy="19.2" r="1.8"/></svg></div><span class="label">Project mngmt</span></div>
      <div class="tile"><div class="box"><svg viewBox="0 0 24 24"><path d="M12 1.5a7 7 0 0 0-4 12.8V17h8v-2.7A7 7 0 0 0 12 1.5z"/><rect x="8.5" y="18.5" width="7" height="1.8"/><rect x="9.5" y="21" width="5" height="1.5"/></svg></div><span class="label">Energy</span></div>

      <div class="tile start2"><div class="box"><svg viewBox="0 0 24 24"><path d="M9 2h7l4 4v12H9z"/><path d="M4 6h3.5v14H16v2H4z"/></svg></div><span class="label">Reports</span></div>
      <div class="tile"><div class="box"><svg viewBox="0 0 24 24"><path d="M2 3h2v16h18v2H2z"/><rect x="6" y="11" width="2" height="6"/><rect x="10" y="7" width="2" height="10"/><rect x="14" y="9" width="2" height="8"/><rect x="18" y="5" width="2" height="12"/></svg></div><span class="label">Analytics</span></div>
      <div class="tile"><div class="box"><svg viewBox="0 0 24 24"><rect x="2" y="4" width="20" height="2.2"/><rect x="2" y="11" width="20" height="2.2"/><rect x="2" y="18" width="20" height="2.2"/><rect x="14" y="2" width="3" height="6" rx="1"/><rect x="6" y="9" width="3" height="6" rx="1"/><rect x="12" y="16" width="3" height="6" rx="1"/></svg></div><span class="label">Configuration</span></div>
      <div class="tile"><div class="box"><svg viewBox="0 0 24 24"><circle cx="12" cy="12" r="7.5" fill="none" stroke="#f6ecd0" stroke-width="5" stroke-dasharray="3.4 2.5"/><circle cx="12" cy="12" r="6.5"/><circle cx="12" cy="12" r="2.8" fill="#34343e"/></svg></div><span class="label">Settings</span></div>
    </div>
  </div>

  <nav class="dock">
    <span class="dock-btn home"><svg viewBox="0 0 24 24"><path d="M12 3l10 8.5-1.4 1.6L19 11.8V21h-5v-6h-4v6H5v-9.2l-1.6 1.3L2 11.5z"/></svg></span>
    <span class="dock-btn apps"><svg viewBox="0 0 24 24"><g><circle cx="5" cy="5" r="2"/><circle cx="12" cy="5" r="2"/><circle cx="19" cy="5" r="2"/><circle cx="5" cy="12" r="2"/><circle cx="12" cy="12" r="2"/><circle cx="19" cy="12" r="2"/><circle cx="5" cy="19" r="2"/><circle cx="12" cy="19" r="2"/><circle cx="19" cy="19" r="2"/></g></svg></span>
  </nav>
</section>

<section class="window window--property">
  <div class="dots"><span class="y"></span><span class="r"></span><span class="g"></span></div>
  <div class="brand"><i></i>Domora</div>
  <div class="theme-toggle"><span class="off"></span><svg width="11" height="11" viewBox="0 0 24 24"><path fill="#fff" d="M14 2a10 10 0 1 0 8 15A9 9 0 0 1 14 2z"/></svg></div>
  <div class="welcome">Welcome, <b>Rafe Dalton</b></div>
  <div class="avatar" role="img" aria-label="User profile photo"></div>

  <h1 class="page-title"><span class="back"><svg width="7" height="7" viewBox="0 0 24 24"><path d="M15 3l3 3-6 6 6 6-3 3-9-9z" fill="#26262f"/></svg></span>Cedar Tower</h1>

  <div class="tabs">
    <span class="tab current" style="width:99px">General information</span>
    <span class="tab" style="width:94px">Organization chart</span>
    <span class="tab" style="width:74px">Tenant List</span>
    <span class="tab" style="width:81px">Property Assets</span>
    <span class="tab" style="width:81px">Contractor list</span>
    <span class="tab" style="width:99px">Compliance mngmt</span>
    <span class="tab" style="width:94px">Maint. Work orders</span>
    <span class="tab" style="width:71px">Work orders</span>
    <span class="tab" style="width:79px">Purchase orders</span>
    <span class="tab" style="width:47px">Files</span>
  </div>

  <article class="info-card">
    <h2>General information</h2>
    <span class="edit-link"><svg viewBox="0 0 24 24"><path d="M3 5h9v2H5v12h12v-7h2v9H3z" fill="#1a8cff"/><path d="M18 2l4 4-10 10H8v-4z" fill="#1a8cff"/></svg>Property Edit</span>
    <dl class="fields">
      <div class="field"><dt>Province</dt><dd>Brisith Columbia</dd></div>
      <div class="field"><dt>City</dt><dd>Ridgemoor</dd></div>
      <div class="field"><dt>Address</dt><dd>48 Harbourline Road, Vancouver, BC</dd></div>
      <div class="field"><dt>GPS Addresse</dt><dd>49.2741183 : -123.1052946000001</dd></div>
      <div class="field"><dt>Postal Code</dt><dd>V6Q 2K8</dd></div>
      <div class="field"><dt>Date Build</dt><dd>07/01/1980</dd></div>
      <div class="field"><dt>Area (sq.ft)</dt><dd>1500000.00</dd></div>
      <div class="field"><dt>Lot Size</dt><dd>1500000.00</dd></div>
      <div class="field"><dt>Zoning</dt><dd>CD1</dd></div>
      <div class="field"><dt>Structure type</dt><dd>Steel and concrete</dd></div>
      <div class="field"><dt>Building height</dt><dd>250 mt</dd></div>

      <div class="field"><dt>Clear height</dt><dd>45 mt</dd></div>
      <div class="field"><dt>Floor loading capacity</dt><dd>50</dd></div>
      <div class="field"><dt>Number of floors</dt><dd>30</dd></div>
      <div class="field"><dt>Number of tenants</dt><dd>30</dd></div>
      <div class="field"><dt>Suites</dt><dd>150</dd></div>
      <div class="field"><dt>Typical bay size</dt><dd>-</dd></div>
      <div class="field"><dt>Building envelope</dt><dd>None</dd></div>
      <div class="field"><dt>Parking</dt><dd>Underground + surface</dd></div>
      <div class="field"><dt>Parking ration/N. of stalls</dt><dd>6</dd></div>
      <div class="field"><dt>Sprinkler protected</dt><dd>Yes</dd></div>
      <div class="field"><dt>Sprinkler ESFR</dt><dd>No</dd></div>

      <div class="field"><dt>Sprinkler capacity (gpm)</dt><dd>No</dd></div>
      <div class="field"><dt>Fire alarm panel</dt><dd>Yes</dd></div>
      <div class="field"><dt>Fire alarm monitored</dt><dd>Yes</dd></div>
      <div class="field"><dt>Máximum electrical capacity (Amps)</dt><dd>2500</dd></div>
      <div class="field"><dt>Building back-up power source</dt><dd>Yes</dd></div>
      <div class="field"><dt>Number of elevators</dt><dd>30</dd></div>
      <div class="field"><dt>Number of escalators</dt><dd>5</dd></div>
      <div class="field"><dt>Roof construction</dt><dd>EPDM</dd></div>
      <div class="field"><dt>Roof insulation</dt><dd>-</dd></div>
      <div class="field"><dt>Utility meters</dt><dd>-</dd></div>
      <div class="field"><dt>Aditional information</dt><dd>-</dd></div>
    </dl>
  </article>

  <div class="photo p1" role="img" aria-label="Night view of the tower and neighbouring high-rises"></div>
  <div class="photo p2" role="img" aria-label="Residential courtyard with outdoor swimming pool"></div>
  <div class="photo p3" role="img" aria-label="Bright furnished apartment living room"></div>
  <div class="photo p4" role="img" aria-label="Rooftop terrace with modern canopy under blue sky"></div>

  <nav class="dock">
    <span class="dock-btn home"><svg viewBox="0 0 24 24"><path d="M12 3l10 8.5-1.4 1.6L19 11.8V21h-5v-6h-4v6H5v-9.2l-1.6 1.3L2 11.5z"/></svg></span>
    <span class="dock-btn apps"><svg viewBox="0 0 24 24"><g><circle cx="5" cy="5" r="2"/><circle cx="12" cy="5" r="2"/><circle cx="19" cy="5" r="2"/><circle cx="5" cy="12" r="2"/><circle cx="12" cy="12" r="2"/><circle cx="19" cy="12" r="2"/><circle cx="5" cy="19" r="2"/><circle cx="12" cy="19" r="2"/><circle cx="19" cy="19" r="2"/></g></svg></span>
  </nav>
</section>

</body>
</html>
```